Money Mindset Podcast needs fun, creative cover art

Launching a new podcast called 'Turning Your Thoughts Toward Savings' - aimed at an audience 30-50 who are interested in the practicalities of managing their money but also the more mental and emotional aspects.
Looking for something not too serious, warm and friendly.

Must be easy to read on phone screens
3000 x 3000 in size
Avoid currency symbols $, £ etc, as may have an international audience

Target Market(s)

Podcast listeners age 30-50 starting in the UK but then worldwide. Probably 60:40 female bias

Industry/Entity Type

Life Coaching

Font styles to use
Serif
Sans Serif

Colors
cadf82
fee18a
acd037
85cae6
eea4c8
f59195
85acd3

Requirements
Must have
• Simple, clear design. Easy to read on variety of devices. 3000 x 3000
Appeal to those with a spiritual or emotional interests
Nice to have
• Stand out among other money related podcasts
Maybe play around with clouds, lightbulbs and clearing skies
Should not have
• Currency symbols such as $ or £
Be too corporate or bank like
Stock images

```html
<!DOCTYPE html>
<html lang="en">
<head>
<meta charset="utf-8">
<title>Turning Your Thoughts Toward Savings</title>
<link rel="stylesheet" href="https://fonts.googleapis.com/css2?family=Forum&display=swap">
<style>
  :root {
    --sky-deep: #2e5688;
    --sky-mid: #85acd3;
    --sky-light: #85cae6;
    --sun-glow: #fee18a;
    --blush: #eea4c8;
    --coral: #f59195;
    --title-yellow: #fee18a;
    --title-white: #ffffff;
    --title-shadow: rgba(30, 55, 95, 0.45);
  }
  html, body {
    margin: 0;
    padding: 0;
    width: 1200px;
    height: 1200px;
    overflow: hidden;
    background: var(--sky-deep);
  }
  .cover {
    position: relative;
    width: 1200px;
    height: 1200px;
    overflow: hidden;
  }
  .cover__scene {
    position: absolute;
    inset: 0;
    background:
      radial-gradient(ellipse 380px 300px at 50% 72%, #fff8dc 0%, var(--sun-glow) 30%, rgba(254,225,138,0.35) 60%, rgba(254,225,138,0) 100%),
      radial-gradient(ellipse 700px 420px at 10% 100%, rgba(238,164,200,0.7) 0%, rgba(238,164,200,0) 100%),
      radial-gradient(ellipse 700px 420px at 90% 100%, rgba(245,145,149,0.6) 0%, rgba(245,145,149,0) 100%),
      linear-gradient(180deg, var(--sky-deep) 0%, #4a78aa 35%, var(--sky-mid) 62%, var(--sky-light) 100%);
  }
  .cover__title {
    position: absolute;
    inset: 0;
    width: 1200px;
    height: 1200px;
  }
  .title-line {
    font-family: "Forum", "Times New Roman", serif;
    font-size: 140px;
    stroke-width: 2.5px;
    paint-order: stroke fill;
    filter: drop-shadow(0 4px 6px var(--title-shadow));
  }
  .title-line--accent { fill: var(--title-yellow); stroke: var(--title-yellow); }
  .title-line--white { fill: var(--title-white); stroke: var(--title-white); }
</style>
</head>
<body>
  <main class="cover">
    <div class="cover__scene" role="img" aria-label="Soft sky lit by a warm glow, with a lone figure standing in a pool of light"></div>
    <svg class="cover__title" viewBox="0 0 1200 1200" role="img" aria-label="Turning Your Thoughts Toward Savings">
      <text class="title-line title-line--accent" x="600" y="232" text-anchor="middle">TURNING</text>
      <text class="title-line title-line--white" x="600" y="412" text-anchor="middle" textLength="1100" lengthAdjust="spacing">YOUR THOUGHTS</text>
      <text class="title-line title-line--accent" x="600" y="592" text-anchor="middle">TOWARD</text>
      <text class="title-line title-line--accent" x="600" y="772" text-anchor="middle">SAVINGS</text>
    </svg>
  </main>
</body>
</html>
```